Business card design for my company.
I would like the card's background colour to be black. You can also see our web site to get an idea of our brand. https://www.tmwhomecrafting.com.au/
- Name
- Email

```html
<!DOCTYPE html>
<html lang="en">
<head>
<meta charset="utf-8">
<title>TMW Home Crafting – Business Card</title>
<link href="https://fonts.googleapis.com/css2?family=Montserrat:wght@500;600;800&display=swap" rel="stylesheet">
<style>
  :root {
    --stage: #3a3a3a;
    --card: #1e1e1e;
    --green: #0e9444;
    --white: #f2f2f2;
    --muted: #d9d9d9;
    --emboss: #3c3c3c;
  }
  * { margin: 0; padding: 0; box-sizing: border-box; }
  html, body { width: 1200px; height: 875px; overflow: hidden; }
  body {
    background: var(--stage);
    font-family: "Montserrat", sans-serif;
    display: flex;
    flex-direction: column;
    align-items: center;
    justify-content: center;
    gap: 60px;
  }
  .card {
    position: relative;
    width: 600px;
    height: 343px;
    background: var(--card);
    border-radius: 18px;
    overflow: hidden;
  }
  /* Front */
  .card--front { display: flex; align-items: center; justify-content: center; }
  .brand { display: flex; align-items: center; gap: 14px; }
  .brand__square { width: 22px; height: 22px; flex: none; }
  .brand__name { font-weight: 800; letter-spacing: 0.04em; text-transform: uppercase; white-space: nowrap; }
  .card--front .brand__square { background: var(--emboss); }
  .card--front .brand__name { color: var(--emboss); font-size: 36px; }

  /* Back */
  .card--back .brand {
    position: absolute; left: 48px; top: 118px; flex-direction: column; align-items: flex-start; gap: 12px;
  }
  .card--back .brand__square { background: var(--green); }
  .card--back .brand__name { color: var(--white); font-size: 24px; line-height: 1.15; width: 200px; white-space: normal; }
  .divider {
    position: absolute; left: 270px; top: 66px; width: 2px; height: 160px; background: var(--green);
  }
  .contact { position: absolute; left: 298px; top: 62px; right: 24px; }
  .contact__name { color: var(--green); font-size: 26px; font-weight: 800; letter-spacing: 0.02em; text-transform: uppercase; }
  .contact__role { color: var(--muted); font-size: 15px; font-weight: 500; margin: 2px 0 14px; }
  .contact__list { list-style: none; }
  .contact__item { display: flex; align-items: center; gap: 10px; color: var(--muted); font-size: 14px; font-weight: 500; margin-bottom: 7px; white-space: nowrap; }
  .contact__item svg { width: 13px; height: 13px; fill: var(--green); flex: none; }
  .band { position: absolute; left: 0; bottom: 0; height: 12px; }
  .band--green { width: 58%; background: var(--green); }
  .band--white { left: 58%; width: 42%; background: var(--white); }
</style>
</head>
<body>
  <section class="card card--front" aria-label="Card front">
    <div class="brand">
      <span class="brand__square"></span>
      <span class="brand__name">TMW Home Crafting</span>
    </div>
  </section>

  <section class="card card--back" aria-label="Card back">
    <div class="brand">
      <span class="brand__square"></span>
      <span class="brand__name">TMW Home Crafting</span>
    </div>
    <div class="divider"></div>
    <div class="contact">
      <h1 class="contact__name">Dean Harlow</h1>
      <p class="contact__role">General Manager</p>
      <ul class="contact__list">
        <li class="contact__item">
          <svg viewBox="0 0 24 24"><path d="M6.6 10.8a15 15 0 0 0 6.6 6.6l2.2-2.2a1 1 0 0 1 1-.25 11.4 11.4 0 0 0 3.6.57 1 1 0 0 1 1 1V20a1 1 0 0 1-1 1A17 17 0 0 1 3 4a1 1 0 0 1 1-1h3.5a1 1 0 0 1 1 1c0 1.25.2 2.45.57 3.6a1 1 0 0 1-.25 1z"/></svg>
          0400 555 123
        </li>
        <li class="contact__item">
          <svg viewBox="0 0 24 24"><path d="M2 5h20v14H2zm2 2v.5l8 5 8-5V7z"/></svg>
          info@tmwhomecrafting.com.au
        </li>
        <li class="contact__item">
          <svg viewBox="0 0 24 24"><path d="M12 2a10 10 0 1 0 0 20 10 10 0 0 0 0-20zm0 2c1 0 2.3 2 2.8 5H9.2C9.7 6 11 4 12 4zm-7.7 7h3c0 .7 0 1.4.1 2H4.3a8 8 0 0 1 0-2zm4.9 0h5.6a15 15 0 0 1 0 2H9.2a15 15 0 0 1 0-2zm7.5 0h3a8 8 0 0 1 0 2h-3c.1-.6.1-1.3 0-2zM12 20c-1 0-2.3-2-2.8-5h5.6C14.3 18 13 20 12 20z"/></svg>
          tmwhomecrafting.com.au
        </li>
        <li class="contact__item">
          <svg viewBox="0 0 24 24"><path d="M12 2a7 7 0 0 0-7 7c0 5 7 13 7 13s7-8 7-13a7 7 0 0 0-7-7zm0 9.5A2.5 2.5 0 1 1 12 6.5a2.5 2.5 0 0 1 0 5z"/></svg>
          Ashcombe Vale, Northland Coast
        </li>
      </ul>
    </div>
    <div class="band band--green"></div>
    <div class="band band--white"></div>
  </section>
</body>
</html>
```